KRTB

We want to design our company brochure. We are a newly established ship management company in Singapore. We manage a fleet of bulk carrier and car carriers. Our job is to run the ships economically and efficiently on behalf of owners of the vessel.
Updates

Project Deadline Extended
Reason: We are not satisfied by the designs as yet. Hence, we are extending the deadline further by 7 days.

Project Deadline Extended
Reason: No designs are up to our expectations

Project Deadline Extended

Target Market(s)

Our target market is various ship owners based all over the world especially in Japan and Europe. These ship owners are looking for third party managers to run their ships economically and efficiently.

Industry/Entity Type

It Company

Colors
32b7a4
33a6d7
00a88f
3276b5
0692cd
86cae6
86cfc6
ebf7f9
edf2f7

Requirements
Must have
• The brochure must have four pages (in form of a folder) with static information, photographs etc with a pocket designed inside to keep printed sheets containing dynamic information.
Write up on our company is attached herewith and also some photographs depicting our ships, crew and the training center.
Information for dynamic sheets is attached in a separate sheets.

```html
<!DOCTYPE html>
<html lang="en">
<head>
<meta charset="utf-8">
<title>KRTB Brochure Spread</title>
<link href="https://fonts.googleapis.com/css2?family=Open+Sans:wght@400;600;700&display=swap" rel="stylesheet">
<style>
:root{
  --bg:#e4e5e7;
  --page:#ffffff;
  --blue:#1d5ea8;
  --blue-light:#3276b5;
  --text:#4a4d52;
  --rule:#c9ccd1;
}
*{margin:0;padding:0;box-sizing:border-box}
html,body{width:1200px;height:847px;overflow:hidden;background:var(--bg);font-family:"Open Sans",Arial,sans-serif;color:var(--text)}
.spread{position:absolute;left:50px;top:110px;width:1100px;height:627px;display:flex;box-shadow:0 10px 30px rgba(0,0,0,.18)}
.page{position:relative;width:550px;height:627px;background:var(--page);overflow:hidden}
.page--left{border-bottom:9px solid var(--blue);border-left:6px solid var(--blue)}
.page--right{border-bottom:9px solid var(--blue);border-right:6px solid var(--blue);background:linear-gradient(90deg,#e9eaec 0,#fff 40px)}
.top-band{position:absolute;left:0;top:0;width:100%;height:60px}
.heading{position:absolute;font-weight:700;color:var(--blue);font-size:22px;line-height:26px;letter-spacing:.3px}
.about-copy{position:absolute;left:34px;top:86px;width:272px;font-size:8.6px;line-height:11.5px}
.about-copy p{margin-bottom:8px}
.photo{position:absolute;border:3px solid #fff;box-shadow:0 1px 3px rgba(0,0,0,.25)}
.tab{position:absolute;height:24px;color:#fff;font-weight:600;font-size:13.5px;line-height:24px;padding-left:14px;background:var(--blue);clip-path:polygon(0 0,92% 0,100% 100%,0 100%)}
.tick{display:inline-block;width:12px;height:10px;margin-right:12px;vertical-align:middle}
.services{position:absolute;left:30px;top:398px;list-style:none;font-size:12px;line-height:16px;font-weight:600}
.services > li{margin-bottom:5px}
.services .sub-head{color:var(--blue);font-weight:700;font-size:12px;line-height:16px;margin:2px 0 6px 24px}
.services ul{list-style:none;margin-left:44px;border-left:1px solid var(--rule);font-size:10.5px;line-height:14px}
.services ul li{margin-bottom:3px;padding-left:6px}
.initiatives{position:absolute;left:42px;top:224px;width:482px;list-style:none;font-size:9.8px;line-height:12.5px}
.initiatives li{display:flex;margin-bottom:5px}
.initiatives .tick{flex:none;margin-top:1px}
.divider-band{position:absolute;left:0;top:380px;width:100%;height:20px;background:linear-gradient(180deg,#cfd2d6,#eef0f2)}
.commitment-copy{position:absolute;left:48px;top:448px;width:250px;font-size:11px;line-height:15px;text-align:justify}
</style>
</head>
<body>
<div class="spread">

  <section class="page page--left">
    <svg class="top-band" viewBox="0 0 550 60" preserveAspectRatio="none" aria-hidden="true">
      <polygon points="0,34 550,0 550,6 0,48" fill="var(--blue)"/>
      <polygon points="0,48 550,6 550,10 0,52" fill="var(--blue-light)" opacity=".5"/>
    </svg>

    <h1 class="heading" style="left:34px;top:58px">ABOUT US</h1>
    <div class="about-copy">
      <p>Keelridge Marine Services Pte. Ltd. established in Singapore in 2012 as a Ship Management company with a clear objective to provide quality service to the Ship Owners while maintaining a fine balance and harmony between cost, efficient operation and giving a humane touch to the Ship Management.</p>
      <p>With this philosophy Keelridge Marine Services Pte. Ltd was formed and was chosen as a dependable ally by Harbourline Group who have trusted us for the upkeep and safe operation of their ships for majority of their existing fleet and all new building vessels.</p>
      <p>We have a vision – to contribute to the ship management business its lost pride and glory by running Clean, Safe and Happy Ships ethically.</p>
      <p>Company is headed by Mr. Arun Mehra who has more than 20 years of sea and shore based experience in various positions in the Shipping industry with majority of time spent ashore in key management position. KRTB is his brainchild and a reflection of his youthful and energetic persona. Like minded professionals were chosen right from the inception who have become the corner stones of the organization to build a strong yet dynamic entity.</p>
    </div>

    <div class="photo" role="img" aria-label="Car carrier vessel at sea" style="left:318px;top:40px;width:200px;height:92px;background:linear-gradient(180deg,#b9cfe0 0,#e8eef2 55%,#5b7f98 100%)"></div>
    <div class="photo" role="img" aria-label="Crew in red survival suits on deck" style="left:318px;top:140px;width:200px;height:96px;background:linear-gradient(180deg,#f0f0f0 0,#c9413c 45%,#a52e2b 100%)"></div>
    <div class="photo" role="img" aria-label="Bulk carrier at anchor" style="left:318px;top:244px;width:200px;height:100px;background:linear-gradient(180deg,#c7d3dc 0,#dfe5e9 50%,#3d4a55 75%,#7e96a8 100%)"></div>
    <div class="photo" role="img" aria-label="Crew in safety gear inside a car deck" style="left:318px;top:352px;width:200px;height:118px;background:linear-gradient(180deg,#6d6a60 0,#8f8a7c 50%,#4a4944 100%)"></div>

    <div class="tab" style="left:0;top:364px;width:200px">SERVICES OFFERED</div>
    <ul class="services">
      <li><svg class="tick" viewBox="0 0 12 10"><path d="M1 5l3.5 3.5L11 1" fill="none" stroke="var(--blue)" stroke-width="2"/></svg>Ship Management</li>
      <li><svg class="tick" viewBox="0 0 12 10"><path d="M1 5l3.5 3.5L11 1" fill="none" stroke="var(--blue)" stroke-width="2"/></svg>Technical Solutions</li>
      <li class="sub-head">An array of technical solutions for the<br>shipping world</li>
      <li><ul>
        <li><svg class="tick" viewBox="0 0 12 10"><path d="M1 5l3.5 3.5L11 1" fill="none" stroke="var(--blue)" stroke-width="2"/></svg>Technical Consultancy</li>
        <li><svg class="tick" viewBox="0 0 12 10"><path d="M1 5l3.5 3.5L11 1" fill="none" stroke="var(--blue)" stroke-width="2"/></svg>New Building Supervision</li>
        <li><svg class="tick" viewBox="0 0 12 10"><path d="M1 5l3.5 3.5L11 1" fill="none" stroke="var(--blue)" stroke-width="2"/></svg>Pre-Purchase Surveys</li>
        <li><svg class="tick" viewBox="0 0 12 10"><path d="M1 5l3.5 3.5L11 1" fill="none" stroke="var(--blue)" stroke-width="2"/></svg>On-Site Supervision</li>
        <li><svg class="tick" viewBox="0 0 12 10"><path d="M1 5l3.5 3.5L11 1" fill="none" stroke="var(--blue)" stroke-width="2"/></svg>Dry Docking</li>
        <li><svg class="tick" viewBox="0 0 12 10"><path d="M1 5l3.5 3.5L11 1" fill="none" stroke="var(--blue)" stroke-width="2"/></svg>Condition Surveys</li>
        <li><svg class="tick" viewBox="0 0 12 10"><path d="M1 5l3.5 3.5L11 1" fill="none" stroke="var(--blue)" stroke-width="2"/></svg>Port Captaincy</li>
      </ul></li>
    </ul>
  </section>

  <section class="page page--right">
    <svg class="top-band" viewBox="0 0 550 60" preserveAspectRatio="none" aria-hidden="true">
      <polygon points="0,0 550,0 550,4 0,44" fill="var(--blue)"/>
    </svg>

    <div class="photo" role="img" aria-label="Office corridor with company sign" style="left:20px;top:24px;width:510px;height:162px;background:linear-gradient(90deg,#dfe3e8 0,#f4f2ee 40%,#d9b9a0 70%,#5c4a44 100%)"></div>

    <div class="tab" style="left:30px;top:194px;width:130px">INITIATIVES</div>
    <ul class="initiatives">
      <li><svg class="tick" viewBox="0 0 12 10"><path d="M1 5l3.5 3.5L11 1" fill="none" stroke="var(--blue)" stroke-width="2"/></svg><span>Started own in house training institute in Manila to train our staff and keep them abreast of new developments in shipping industry.</span></li>
      <li><svg class="tick" viewBox="0 0 12 10"><path d="M1 5l3.5 3.5L11 1" fill="none" stroke="var(--blue)" stroke-width="2"/></svg><span>ECDIS installation started on board in order to ensure smooth transition to paperless navigation with proper training to ship staff in our training center.</span></li>
      <li><svg class="tick" viewBox="0 0 12 10"><path d="M1 5l3.5 3.5L11 1" fill="none" stroke="var(--blue)" stroke-width="2"/></svg><span>Commenced Internet facility on board all our vessels. 20 mb data being given free to each crew every month.</span></li>
      <li><svg class="tick" viewBox="0 0 12 10"><path d="M1 5l3.5 3.5L11 1" fill="none" stroke="var(--blue)" stroke-width="2"/></svg><span>Special emphasis on crew welfare with supply of fitness and entertainment equipment on board.</span></li>
      <li><svg class="tick" viewBox="0 0 12 10"><path d="M1 5l3.5 3.5L11 1" fill="none" stroke="var(--blue)" stroke-width="2"/></svg><span>Assistance like free telephone cards, internet cards, cash donation provided to staff in case of a natural calamity in home country.</span></li>
    </ul>

    <div class="divider-band"></div>

    <h2 class="heading" style="left:48px;top:414px">COMMITMENT</h2>
    <p class="commitment-copy">The company believes that good training, motivation and emphasis on human values are essential for long term success. Consequently, the company is committed to providing an ideal working environment both in its offices and on ships.</p>

    <div class="photo" role="img" aria-label="Bulk carrier alongside a quay with crane" style="left:322px;top:414px;width:200px;height:126px;background:linear-gradient(180deg,#b6c6d4 0,#d8dde0 35%,#2c2d31 60%,#a5362f 80%,#c7b58c 100%)"></div>
  </section>

</div>
</body>
</html>
```